Business Card Design Project

Company Name - Solvane Care

Wellness consulting and training company. Run through a medical centre.

Main colour themes are orange and blue, as in the logo. Want to replicate same effect with business cards.

To give a sense of freedom and potential as per the company name.

Want the business card to be in line with stationary design, which I have launched as well.

Double sided with design and colour on one side and details on other side.

Reason: Need business card and stationary design to be teed up.

Target Market(s)

35 to 65 age group.
New age and trendy

Industry/Entity Type

Training

Requirements
Must have
• Colours orange and blue as per logo
Nice to have
• Design to be similar to stationary design, letterhead and envelopes

```html
<!DOCTYPE html>
<html lang="en">
<head>
<meta charset="utf-8">
<title>Solvane Care – Stationery Set</title>
<link href="https://fonts.googleapis.com/css2?family=Source+Sans+3:wght@400;600&family=Marcellus+SC&display=swap" rel="stylesheet">
<style>
  :root{
    --blue:#1550a3;
    --orange:#f26a1f;
    --paper:#ffffff;
    --ink:#333333;
    --muted:#555555;
    --backdrop:#474747;
  }
  *{box-sizing:border-box;margin:0;padding:0}
  html,body{width:1200px;height:727px;overflow:hidden;background:var(--backdrop)}
  .canvas{position:relative;width:1200px;height:727px}
  .sheet{position:absolute;background:var(--paper);overflow:hidden}
  .brand{position:absolute;font-family:"Source Sans 3",sans-serif;font-weight:400;color:var(--blue);white-space:nowrap;display:flex;align-items:center;gap:6px}
  .brand-mark{display:inline-block;background:var(--orange)}
  .contacts{position:absolute;font-family:"Marcellus SC",serif;color:var(--muted);list-style:none;white-space:nowrap}
  .contacts li{display:flex;align-items:center;gap:7px}
  .contacts svg{fill:var(--blue);flex:none}
  .address{position:absolute;font-family:"Marcellus SC",serif;color:var(--muted);white-space:nowrap}
  .wave-band{position:absolute;left:0;bottom:0;width:100%;background:linear-gradient(100deg,var(--orange) 0%,var(--orange) 18%,var(--blue) 48%,var(--blue) 100%)}

  /* letterhead */
  .letterhead{left:17px;top:17px;width:538px;height:693px}
  .letterhead .brand{left:39px;top:56px;font-size:29px}
  .letterhead .brand-mark{width:11px;height:11px}
  .letterhead .contacts{left:343px;top:62px;font-size:11px;line-height:15px}
  .letter{position:absolute;left:56px;top:166px;width:426px;font-family:"Source Sans 3",sans-serif;font-size:9.9px;line-height:10.9px;color:var(--ink)}
  .letter p{margin-bottom:11px;text-align:justify}
  .letter .recipient,.letter .closing{text-align:left}
  .signature{position:absolute;left:58px;top:490px;width:56px;height:26px;background:linear-gradient(90deg,#c9c3dd,#e6e2f0);border-radius:3px}
  .seal{position:absolute;left:116px;top:478px;width:44px;height:44px;border-radius:50%;background:#d5ecee}
  .letterhead .wave-band{height:70px}

  /* compliment slip */
  .slip{left:580px;top:17px;width:603px;height:261px}
  .slip .brand{left:25px;top:62px;font-size:27px}
  .slip .brand-mark{width:10px;height:10px}
  .slip .contacts{left:26px;top:126px;font-size:11px;line-height:13px}
  .slip .address{left:26px;top:172px;font-size:11px;line-height:13px}
  .slip .wave-band{height:50px}

  /* envelope */
  .envelope{left:580px;top:293px;width:603px;height:267px}
  .envelope .flap{position:absolute;left:0;top:0;width:100%;height:112px;background:var(--blue)}
  .envelope .brand{left:229px;top:62px;font-size:28px;color:var(--paper)}
  .envelope .brand-mark{width:10px;height:10px;background:var(--paper)}

  /* business card */
  .card-front{left:641px;top:572px;width:240px;height:138px}
  .card-front .brand{left:11px;top:40px;font-size:16px;gap:4px}
  .card-front .brand-mark{width:6px;height:6px}
  .holder{position:absolute;right:12px;top:47px;text-align:right;font-family:"Marcellus SC",serif}
  .holder-name{font-size:9px;color:var(--blue)}
  .holder-role{font-size:6.5px;color:var(--orange)}
  .card-front .rule{position:absolute;left:10px;right:10px;top:76px;height:1px;background:#b8b8b8}
  .card-front .contacts{left:10px;top:83px;font-size:6px;line-height:8px}
  .card-front .contacts li{gap:4px}
  .card-front .address{right:12px;top:83px;font-size:6.2px;line-height:8px;text-align:right}
  .card-front .wave-band{height:28px}
  .card-back{left:899px;top:572px;width:241px;height:138px;background:var(--blue)}
  .card-back .brand{left:58px;top:78px;font-size:23px;color:var(--paper);gap:5px}
  .card-back .brand-mark{width:8px;height:8px;background:var(--paper)}
</style>
</head>
<body>
<main class="canvas">

  <section class="sheet letterhead">
    <div class="brand"><span>Solvane Care</span><span class="brand-mark"></span></div>
    <ul class="contacts">
      <li><svg width="10" height="9" viewBox="0 0 10 9"><path d="M1 2c0-1 1-1.5 4-1.5S9 1 9 2v1H7V2H3v1H1zM2 4h6l1 4H1z"/></svg>+61 7 3014 5520</li>
      <li><svg width="10" height="8" viewBox="0 0 10 8"><path d="M0 0h10v8H0zM1 1.2v.6l4 2.8 4-2.8v-.6L5 4z" fill-rule="evenodd"/></svg>HELLO@SOLVANECARE.COM</li>
      <li><svg width="10" height="9" viewBox="0 0 10 9"><path d="M0 0h10v7H6v1h1v1H3V8h1V7H0zM1 1v5h8V1z" fill-rule="evenodd"/></svg>WWW.SOLVANECARE.COM</li>
    </ul>
    <article class="letter">
      <p class="recipient">Alex Marlow<br>48 Kestrel Ave<br>Brisbane, Australia</p>
      <p class="recipient">Dear Alex Marlow,</p>
      <p>Lorem ipsum dolor sit amet, consectetuer adipiscing elit. Praesent mattis eros a tellus. Quisque leo tortor, commodo id, dapibus et, lacinia et, justo. Ut urna sapien, dictum eu, cursus vel, consectetuer tincidunt, eros. Etiam in libero. Etiam tempor. Maecenas ligula felis, commodo eget, scelerisque id, suscipit nec, odio. Vivamus commodo, magna in mollis feugiat, felis nisl dapibus dolor, eu blandit orci nulla in orci. Cras felis ipsum, mollis at, semper et, tincidunt id, ipsum. Ut consectetuer elit nec elit. Cras luctus molestie ligula. In gravida tempor nunc.</p>
      <p>Curabitur nisl ligula, pulvinar et, volutpat non, porta a, ipsum. Donec tristique ante at est. Pellentesque volutpat est non diam. Aenean vel velit. Suspendisse facilisis nisl et massa. Mauris nec erat. Pellentesque luctus arcu ut dui. Proin suscipit lorem id augue. Maecenas eget ipsum nec orci convallis viverra. Suspendisse potenti. Donec sed enim. Ut et turpis. Ut mattis enim nec nisl. Ut quam. Pellentesque lobortis vehicula risus.</p>
      <p>Etiam massa erat, tempor et, elementum fringilla, pellentesque ac, odio. Cras sed felis. Aliquam erat volutpat. Etiam tristique. Donec pellentesque, nulla semper adipiscing faucibus, nibh augue semper sapien, eget feugiat dui massa et urna. Nullam ac arcu. Quisque interdum. Morbi tristique sagittis arcu. Phasellus euismod ante eget risus. Nam convallis rutrum augue. Pellentesque placerat ultrices tellus.</p>
      <p class="closing">Your Sincerely,<br>Leon Varga.</p>
    </article>
    <div class="signature" role="img" aria-label="Handwritten signature"></div>
    <div class="seal" role="img" aria-label="Company seal"></div>
    <div class="wave-band" role="img" aria-label="Orange and blue decorative band along the foot of the page"></div>
  </section>

  <section class="sheet slip">
    <div class="brand"><span>Solvane Care</span><span class="brand-mark"></span></div>
    <ul class="contacts">
      <li><svg width="10" height="9" viewBox="0 0 10 9"><path d="M1 2c0-1 1-1.5 4-1.5S9 1 9 2v1H7V2H3v1H1zM2 4h6l1 4H1z"/></svg>+61 7 3014 5520</li>
      <li><svg width="10" height="8" viewBox="0 0 10 8"><path d="M0 0h10v8H0zM1 1.2v.6l4 2.8 4-2.8v-.6L5 4z" fill-rule="evenodd"/></svg>HELLO@SOLVANECARE.COM</li>
      <li><svg width="10" height="9" viewBox="0 0 10 9"><path d="M0 0h10v7H6v1h1v1H3V8h1V7H0zM1 1v5h8V1z" fill-rule="evenodd"/></svg>WWW.SOLVANECARE.COM</li>
    </ul>
    <p class="address">Here your companyor<br>home address</p>
    <div class="wave-band" role="img" aria-label="Orange and blue decorative band along the foot of the slip"></div>
  </section>

  <section class="sheet envelope">
    <div class="flap" role="img" aria-label="Blue envelope flap"></div>
    <div class="brand"><span>Solvane Care</span><span class="brand-mark"></span></div>
  </section>

  <section class="sheet card-front">
    <div class="brand"><span>Solvane Care</span><span class="brand-mark"></span></div>
    <div class="holder">
      <p class="holder-name">Mara Quinlan</p>
      <p class="holder-role">Manager</p>
    </div>
    <div class="rule"></div>
    <ul class="contacts">
      <li><svg width="6" height="6" viewBox="0 0 10 9"><path d="M1 2c0-1 1-1.5 4-1.5S9 1 9 2v1H7V2H3v1H1zM2 4h6l1 4H1z"/></svg>+61 7 3014 5520</li>
      <li><svg width="6" height="5" viewBox="0 0 10 8"><path d="M0 0h10v8H0zM1 1.2v.6l4 2.8 4-2.8v-.6L5 4z" fill-rule="evenodd"/></svg>HELLO@SOLVANECARE.COM</li>
      <li><svg width="6" height="6" viewBox="0 0 10 9"><path d="M0 0h10v7H6v1h1v1H3V8h1V7H0zM1 1v5h8V1z" fill-rule="evenodd"/></svg>WWW.SOLVANECARE.COM</li>
    </ul>
    <p class="address">Here your companyor<br>home address</p>
    <div class="wave-band" role="img" aria-label="Orange and blue decorative band along the foot of the card"></div>
  </section>

  <section class="sheet card-back">
    <div class="brand"><span>Solvane Care</span><span class="brand-mark"></span></div>
  </section>

</main>
</body>
</html>
```